Velk Partners Building Business Cards

We need a business card that reflects our business as "Solar Experts" in San Diego. Browse our website www.velkpartners.example our License needs to be displayed as "CSLB# 3867140" our phone number is (619) 555-0187

Save thousands on your electric bills and increase the value of your home while helping to protect the environment. Our solar installation experts will help you design the system that's right for you, using only the highest quality equipment that will look great and give you ideal performance. Our goal is to make you energy independent, and get your electric bill to 0.

Paul Osterby
(619) 555-0187
paul@velkpartners.example

Target Market(s)

Home owners in san diego looking for solar

Industry/Entity Type

Solar Energy

Contact Information for Business Card

Paul Osterby
(619) 555-0187
paul@velkpartners.example

Font styles to use
Other font styles liked:
• Use our logo font

Requirements
Must have
• License needs to be displayed as "CSLB# 3867140" our phone number is (619) 555-0187
Nice to have
• Real images of rooftop home solar in san diego
Should not have
• our business address

```html
<!DOCTYPE html>
<html lang="en">
<head>
<meta charset="utf-8">
<title>Velk Partners Building – Business Cards</title>
<link rel="stylesheet" href="https://fonts.googleapis.com/css2?family=Roboto:wght@400;500;700;900&display=swap">
<style>
  :root {
    --navy: #1f4a8a;
    --navy-deep: #173b72;
    --gold: #f6a821;
    --paper: #ffffff;
    --backdrop: #e9e6e1;
  }
  * { box-sizing: border-box; margin: 0; padding: 0; }
  html, body {
    width: 900px; height: 1200px; overflow: hidden;
    background: var(--backdrop);
    font-family: "Roboto", Arial, sans-serif;
  }
  .sheet { position: relative; width: 900px; height: 1200px; }

  .card {
    position: absolute; left: 90px; width: 720px; height: 420px;
    overflow: hidden;
    box-shadow: 0 6px 18px rgba(0,0,0,0.18);
  }
  .card--front { top: 165px; background: var(--paper); }
  .card--back { top: 630px; background: var(--navy); }

  .brand {
    position: absolute; left: 0; right: 0; text-align: center;
    font-weight: 700; line-height: 1;
  }
  .card--front .brand { top: 70px; color: var(--navy); }
  .card--back .brand { top: 140px; color: var(--paper); }
  .brand__name { display: block; font-size: 60px; letter-spacing: -0.5px; }
  .brand__line { display: block; font-size: 28px; letter-spacing: 3px; margin-top: 12px; text-transform: uppercase; }
  .brand__mark {
    display: inline-block; width: 22px; height: 22px; border-radius: 50%;
    background: currentColor; margin-left: 10px; vertical-align: 8px;
  }

  .contact {
    position: absolute; top: 255px; left: 225px;
    display: grid; grid-template-columns: 150px auto; column-gap: 14px; row-gap: 6px;
    font-size: 17px; align-items: center;
  }
  .contact__name { color: var(--navy); font-weight: 500; font-size: 19px; }
  .contact__role { color: var(--gold); font-size: 16px; }
  .contact__item { display: flex; align-items: center; gap: 10px; color: var(--navy); font-weight: 500; }
  .contact__item svg { width: 18px; height: 18px; flex: none; }

  .credentials {
    position: absolute; top: 335px; left: 0; right: 0; text-align: center;
    font-size: 14px; font-weight: 500; color: var(--navy); letter-spacing: 0.3px;
  }
  .credentials__sep { color: var(--gold); margin: 0 10px; }

  .tagline {
    position: absolute; top: 300px; left: 0; right: 0; text-align: center;
    color: var(--gold); font-size: 18px; font-weight: 500; letter-spacing: 4px;
    text-transform: uppercase;
  }

  .stripe { position: absolute; left: 0; bottom: 0; width: 720px; height: 42px; }
</style>
</head>
<body>
<main class="sheet">
  <section class="card card--front" aria-label="Business card front">
    <div class="brand">
      <span class="brand__name">Velk Partners<span class="brand__mark"></span></span>
      <span class="brand__line">Building</span>
    </div>

    <div class="contact">
      <span class="contact__name">Paul Osterby</span>
      <span class="contact__item">
        <svg viewBox="0 0 24 24"><path fill="var(--gold)" d="M6.6 10.8a15.1 15.1 0 0 0 6.6 6.6l2.2-2.2a1 1 0 0 1 1-.25 11.4 11.4 0 0 0 3.6.57 1 1 0 0 1 1 1V20a1 1 0 0 1-1 1A17 17 0 0 1 3 4a1 1 0 0 1 1-1h3.5a1 1 0 0 1 1 1c0 1.25.2 2.45.57 3.6a1 1 0 0 1-.25 1z"/></svg>
        (619) 555-0187
      </span>
      <span class="contact__role">Managing director</span>
      <span class="contact__item">
        <svg viewBox="0 0 24 24"><rect x="2" y="5" width="20" height="14" rx="2" fill="var(--gold)"/><path d="M3 6l9 7 9-7" fill="none" stroke="#fff" stroke-width="1.8"/></svg>
        paul@velkpartners.example
      </span>
    </div>

    <p class="credentials">
      www.velkpartners.example<span class="credentials__sep">|</span>CSLB# 3867140
    </p>

    <svg class="stripe" viewBox="0 0 720 42" preserveAspectRatio="none" aria-hidden="true">
      <polygon points="0,14 420,14 400,42 0,42" fill="var(--gold)"/>
      <polygon points="420,14 720,14 720,42 400,42" fill="var(--navy)"/>
      <polygon points="404,36 720,36 720,42 400,42" fill="var(--navy-deep)"/>
    </svg>
  </section>

  <section class="card card--back" aria-label="Business card back">
    <div class="brand">
      <span class="brand__name">Velk Partners<span class="brand__mark"></span></span>
      <span class="brand__line">Building</span>
    </div>
    <p class="tagline">Solar Experts · San Diego</p>
  </section>
</main>
</body>
</html>
```